Board Presentation template

Design a simple and clean PowerPoint slide templates for a Board meeting. The slides should have predominantly white backgrounds and use the colors of our Logo (attached): Tones of grey and orange and blue.
The company name is called Keystone Lane Gauging.
It sell, calibrate, service and repair industrial and commercial scales of all types. In particular, Truck scales, floor scales, counting scales and benchtop scales.
There is no website for Keystone Lane Gauging, but we have three affiliates that have their own websites:
https://www.fernwaybalance.example/
https://meadowlarkhandlingandmassing.example/
https://tvbalance.example/
Target Market(s)
Industrial and Commercial Weighing systems
Industry/Entity Type
Look and feel

```html
<!DOCTYPE html>
<html lang="en">
<head>
<meta charset="utf-8">
<title>Keystone Lane Gauging — Board Presentation Template</title>
<link href="https://fonts.googleapis.com/css2?family=Oswald:wght@500;600&family=Figtree:wght@400;500&display=swap" rel="stylesheet">
<style>
  :root{
    --slate:#3b4853;
    --slate-dark:#2e3a44;
    --blue:#2b5f8b;
    --blue-light:#7f9cc4;
    --red:#c93a2c;
    --ink:#3f4348;
    --muted:#5f6469;
    --rule:#e3e6ea;
    --paper:#ffffff;
  }
  *{box-sizing:border-box;margin:0;padding:0}
  html,body{width:1002px;height:1200px;overflow:hidden;background:var(--paper)}
  body{position:relative;font-family:"Figtree",sans-serif;color:var(--ink)}
  .slide{position:absolute;width:466px;height:262px;background:var(--paper);overflow:hidden;box-shadow:0 1px 4px rgba(0,0,0,.18)}
  .col-l{left:25px}.col-r{left:511px}
  .row1{top:31px}.row2{top:322px}.row3{top:612px}.row4{top:899px}
  .corner{position:absolute;left:0;top:0;width:60px;height:60px}
  .slide-title{position:absolute;left:27px;top:22px;font-family:"Oswald",sans-serif;font-weight:600;font-size:16px;letter-spacing:.1px;color:var(--slate);text-transform:uppercase}
  .slide-title em{font-style:normal;color:var(--blue)}
  .brand-tag{position:absolute;right:14px;top:20px;text-align:center;font-family:"Oswald",sans-serif;font-weight:600;font-size:7px;line-height:1.15;color:var(--slate);text-transform:uppercase;letter-spacing:.3px}
  .page-no{position:absolute;right:18px;bottom:6px;width:14px;height:14px;border:1.2px solid var(--slate);border-radius:50%;font-size:5px;line-height:12px;text-align:center;color:var(--red)}
  .photo{position:absolute;border-radius:8px}

  /* cover */
  .cover-bg{position:absolute;inset:0;background:linear-gradient(120deg,#4a565e 0%,#3a464f 50%,#2f3a42 100%)}
  .cover-text{position:absolute;left:0;width:200px;text-align:center;color:#fff}
  .cover-brand{top:95px;font-family:"Oswald",sans-serif;font-weight:600;font-size:12px;line-height:1.1;letter-spacing:.4px;text-transform:uppercase}
  .cover-title{top:132px;font-family:"Oswald",sans-serif;font-weight:600;font-size:12.5px;line-height:20px;text-transform:uppercase}
  .cover-sub{top:185px;font-size:8px}
  .cover-date{top:211px;font-size:7.5px;letter-spacing:.2px}

  /* about */
  .about-copy{position:absolute;top:55px;font-size:6px;line-height:12.6px;color:var(--ink)}
  .about-shot{position:absolute;top:145px;width:141px;height:85px;border:2px solid #fff;box-shadow:0 0 0 1px #cfd3d8,0 2px 4px rgba(0,0,0,.18);border-radius:7px}

  /* services */
  .services-band{position:absolute;left:0;top:60px;width:163px;height:167px;background:var(--blue);border-top-right-radius:40px}
  .services-card{position:absolute;left:18px;top:82px;width:429px;height:124px;background:#fff;border-radius:10px;box-shadow:0 1px 5px rgba(0,0,0,.15);display:flex}
  .service{position:relative;padding:14px 0 0 17px;border-right:1px solid var(--rule)}
  .service:last-child{border-right:0}
  .service svg{width:22px;height:22px;display:block}
  .service h3{margin-top:12px;font-family:"Figtree",sans-serif;font-weight:500;font-size:7.2px;line-height:14.3px;color:var(--blue);text-transform:uppercase;letter-spacing:.2px}
  .service p{margin-top:6px;font-size:6.1px;line-height:12.8px;color:var(--muted)}

  /* metrics */
  .chart{position:absolute;left:0;top:0;width:466px;height:262px}
  .chart text{font-family:"Figtree",sans-serif;fill:var(--ink)}
  .highlights{position:absolute;left:245px;top:72px;width:210px}
  .highlights h3{font-family:"Oswald",sans-serif;font-weight:600;font-size:15px;color:var(--slate);margin-bottom:14px}
  .highlights li{list-style:none;position:relative;padding-left:21px;font-size:7.8px;line-height:14.3px;margin-bottom:9.5px}
  .highlights li svg{position:absolute;left:0;top:3px;width:8px;height:8px}

  /* table */
  .ops-table{position:absolute;left:16px;top:64px;width:434px;height:164px;border-radius:6px;box-shadow:0 1px 4px rgba(0,0,0,.15);border-collapse:collapse;overflow:hidden;font-size:6px;background:#fff}
  .ops-table th{height:22px;background:#f2f4f6;color:var(--blue);font-weight:500;font-size:6.5px;text-align:left;padding-left:14px;letter-spacing:.2px}
  .ops-table td{height:25.7px;padding-left:12px;color:var(--ink)}
  .ops-table th + th,.ops-table td + td{border-left:1px solid var(--rule)}
  .ops-table small{font-size:5px}

  /* affiliates */
  .affiliate{position:absolute;top:65px;width:132px;height:167px;border:1px solid #f0d6d6;border-radius:9px;text-align:center;padding:0 12px}
  .affiliate-name{display:flex;align-items:center;justify-content:center;gap:4px;height:60px;font-family:"Oswald",sans-serif;font-weight:600;font-size:9px;color:var(--slate);text-transform:uppercase;line-height:1.15}
  .affiliate-name i{display:block;width:7px;height:7px;border-radius:50%;background:var(--red);flex:none}
  .affiliate p{font-size:6.6px;line-height:14.8px;color:var(--muted)}

  /* closing */
  .closing-bg{position:absolute;inset:0;background:linear-gradient(135deg,#44515a 0%,#37434c 55%,#2d3840 100%)}
  .closing-brand{position:absolute;left:0;right:0;top:118px;text-align:center;color:#fff;font-family:"Oswald",sans-serif;font-weight:600;font-size:14px;line-height:1.1;text-transform:uppercase;letter-spacing:.4px}
  .closing-thanks{position:absolute;left:0;right:0;top:160px;text-align:center;color:#fff;font-family:"Oswald",sans-serif;font-weight:600;font-size:41px;letter-spacing:.5px}
</style>
</head>
<body>

<svg width="0" height="0" style="position:absolute">
  <defs>
    <symbol id="corner-sweep" viewBox="0 0 60 60">
      <path d="M0 0 H52 C28 4 6 18 0 48 Z" fill="#c93a2c"/>
    </symbol>
    <symbol id="tick-dot" viewBox="0 0 10 10">
      <circle cx="5" cy="5" r="5" fill="#3b4853"/>
      <path d="M2.8 5.2 L4.4 6.7 L7.3 3.6" stroke="#fff" stroke-width="1.3" fill="none" stroke-linecap="round" stroke-linejoin="round"/>
    </symbol>
  </defs>
</svg>

<!-- 01 Cover -->
<section class="slide col-l row1">
  <div class="cover-bg" role="img" aria-label="Dimmed photo of a scale service workshop with a technician beside a service truck"></div>
  <div class="cover-text cover-brand">Keystone Lane<br>Gauging</div>
  <div class="cover-text cover-title">Keystone Lane Gauging<br>Board of Directors Meeting</div>
  <div class="cover-text cover-sub">Performance Review &amp; Strategic Outlook</div>
  <div class="cover-text cover-date">OCTOBER 2025</div>
</section>

<!-- 02 About -->
<section class="slide col-r row1">
  <svg class="corner"><use href="#corner-sweep"/></svg>
  <h2 class="slide-title">About <em>Keystone Lane Gauging</em></h2>
  <div class="brand-tag">Keystone Lane<br>Gauging</div>
  <p class="about-copy" style="left:27px;width:196px">Keystone Lane Gauging specializes in the sales, calibration, service, and repair of industrial and commercial scales of all types. Our expertise covers a full range of weighing solutions — including truck scales, floor scales, counting scales, and benchtop scales — ensuring accuracy, compliance, and operational reliability for our clients.</p>
  <p class="about-copy" style="left:250px;top:58px;width:200px">Backed by decades of experience and trusted industry partnerships, we are committed to precision, performance, and personalized service. Through our affiliate network — Fernway Balance, Meadowlark Handling &amp; Massing, and TV Balance — we deliver comprehensive weighing solutions across diverse sectors.</p>
  <div class="about-shot" style="left:14px;background:linear-gradient(160deg,#9fb3c8,#4c6580)" role="img" aria-label="Photo of a calibration lab with technicians at benchtop scales"></div>
  <div class="about-shot" style="left:163px;background:linear-gradient(160deg,#b8c3cd,#56697a)" role="img" aria-label="Photo of a service bay with a white truck and a scale on a workbench"></div>
  <div class="about-shot" style="left:310px;background:linear-gradient(160deg,#aebccb,#4a5f74)" role="img" aria-label="Photo of a technician repairing scales at a workshop bench"></div>
  <div class="page-no">02</div>
</section>

<!-- 03 Services -->
<section class="slide col-l row2">
  <svg class="corner"><use href="#corner-sweep"/></svg>
  <h2 class="slide-title">Our <em>Services</em></h2>
  <div class="brand-tag">Keystone Lane<br>Gauging</div>
  <div class="services-band"></div>
  <div class="services-card">
    <div class="service" style="width:100px">
      <svg viewBox="0 0 24 24" fill="none" stroke="#2b5f8b" stroke-width="1.1"><circle cx="11" cy="11" r="8"/><circle cx="11" cy="11" r="4"/><path d="M11 1.5v3M11 17.5v3M1.5 11h3M17.5 11h3"/><circle cx="18" cy="18" r="3.5" stroke="#c93a2c"/><path d="M16.5 18l1 1 2-2" stroke="#c93a2c"/></svg>
      <h3>Scale Sales &amp;<br>Installation</h3>
      <p>Supplying a full range<br>of industrial and<br>commercial weighing</p>
    </div>
    <div class="service" style="width:104px">
      <svg viewBox="0 0 24 24" fill="none" stroke="#2b5f8b" stroke-width="1.1"><rect x="3" y="2" width="13" height="18" rx="1"/><path d="M6 7h7M6 10h7M6 13h4"/><circle cx="18" cy="15" r="3.5" stroke="#c93a2c"/><path d="M16.5 18l-1 4 2.5-1.5 2.5 1.5-1-4" stroke="#c93a2c"/></svg>
      <h3>Calibration &amp;<br>Certification</h3>
      <p>Providing precise<br>calibration services to<br>ensure accuracy</p>
    </div>
    <div class="service" style="width:104px">
      <svg viewBox="0 0 24 24" fill="none" stroke="#2b5f8b" stroke-width="1.1"><circle cx="12" cy="12" r="9"/><circle cx="12" cy="12" r="5.5"/><path d="M9 15l5-5M13 9.5l2 2" stroke="#c93a2c"/></svg>
      <h3>Preventive<br>Maintenance</h3>
      <p>Offering scheduled<br>maintenance programs<br>to minimize downtime</p>
    </div>
    <div class="service" style="width:121px">
      <svg viewBox="0 0 24 24" fill="none" stroke="#2b5f8b" stroke-width="1.1"><rect x="2" y="3" width="16" height="14" rx="1"/><path d="M2 6h16"/><circle cx="9" cy="11.5" r="3"/><path d="M17.5 13l4 7h-8z" stroke="#c93a2c"/><path d="M17.5 15.5v2" stroke="#c93a2c"/></svg>
      <h3>Repairs &amp;<br>Troubleshooting</h3>
      <p>Delivering fast, reliable repair<br>services for all makes and<br>models of scales</p>
    </div>
  </div>
  <div class="page-no">03</div>
</section>

<!-- 04 Accuracy -->
<section class="slide col-r row2">
  <svg class="corner"><use href="#corner-sweep"/></svg>
  <h2 class="slide-title">Where Accuracy <em>Meets Expertise</em></h2>
  <div class="brand-tag">Keystone Lane<br>Gauging</div>
  <div class="photo" style="left:21px;top:66px;width:424px;height:159px;border-radius:10px;background:linear-gradient(100deg,#c9d2da 0%,#8e9dab 45%,#5a6a7a 100%)" role="img" aria-label="Photo of a technician calibrating a benchtop scale in a workshop with a service truck behind"></div>
  <div class="page-no">04</div>
</section>

<!-- 05 Performance -->
<section class="slide col-l row3">
  <svg class="corner"><use href="#corner-sweep"/></svg>
  <h2 class="slide-title">Performance <em>Metrics Overview</em></h2>
  <div class="brand-tag">Keystone Lane<br>Gauging</div>
  <svg class="chart" viewBox="0 0 466 262">
    <g stroke="#e3e6ea" stroke-width=".6">
      <line x1="21" y1="62" x2="210" y2="62"/><line x1="21" y1="71" x2="210" y2="71"/>
      <line x1="21" y1="80" x2="210" y2="80"/><line x1="21" y1="89" x2="210" y2="89"/>
      <line x1="21" y1="98" x2="210" y2="98"/><line x1="21" y1="107" x2="210" y2="107"/>
      <line x1="21" y1="116" x2="210" y2="116"/><line x1="21" y1="125" x2="210" y2="125"/>
    </g>
    <rect x="44" y="94" width="13" height="31" fill="#3b4853"/>
    <rect x="66" y="86" width="13" height="39" fill="#2b5f8b"/>
    <rect x="88" y="77" width="13" height="48" fill="#c93a2c"/>
    <rect x="131" y="114" width="13" height="11" fill="#3b4853"/>
    <rect x="154" y="105" width="13" height="20" fill="#2b5f8b"/>
    <rect x="176" y="113" width="13" height="12" fill="#c93a2c"/>
    <g font-size="7" text-anchor="middle">
      <text x="49" y="137">Sales</text><text x="82" y="137">Calibration</text>
      <text x="139" y="137">Repairs</text><text x="178" y="137">Maintenance</text>
    </g>
    <g stroke="#e3e6ea" stroke-width=".6">
      <line x1="21" y1="156" x2="115" y2="156"/><line x1="21" y1="167" x2="115" y2="167"/>
      <line x1="21" y1="178" x2="115" y2="178"/><line x1="21" y1="189" x2="115" y2="189"/>
      <line x1="21" y1="200" x2="115" y2="200"/>
    </g>
    <polyline points="26,196 50,184 77,190 107,167" fill="none" stroke="#3b4853" stroke-width="1.1"/>
    <g fill="#3b4853"><circle cx="26" cy="196" r="1.6"/><circle cx="50" cy="184" r="1.6"/><circle cx="77" cy="190" r="1.6"/><circle cx="107" cy="167" r="1.6"/></g>
    <g font-size="7" text-anchor="middle">
      <text x="30" y="222">2023</text><text x="55" y="222">2024</text><text x="80" y="222">2025</text><text x="104" y="222">2025</text>
    </g>
    <g stroke="#fff" stroke-width=".8">
      <path d="M170 186 L170 153 A33 33 0 0 1 202.5 191.7 Z" fill="#3b4853"/>
      <path d="M170 186 L202.5 191.7 A33 33 0 0 1 143 205 Z" fill="#2b5f8b"/>
      <path d="M170 186 L143 205 A33 33 0 0 1 141.4 169.5 Z" fill="#c93a2c"/>
      <path d="M170 186 L141.4 169.5 A33 33 0 0 1 170 153 Z" fill="#7f9cc4"/>
    </g>
    <g font-size="6.8">
      <circle cx="127" cy="233" r="2" fill="#3b4853"/><text x="131" y="235.5">Truck</text>
      <circle cx="155" cy="233" r="2" fill="#7f9cc4"/><text x="159" y="235.5">Floor</text>
      <circle cx="182" cy="233" r="2" fill="#7f9cc4"/><text x="186" y="235.5">Counting</text>
    </g>
  </svg>
  <div class="highlights">
    <h3>KEY HIGHLIGHTS:</h3>
    <ul>
      <li><svg><use href="#tick-dot"/></svg>+18% increase in calibration service revenue year-over-year</li>
      <li><svg><use href="#tick-dot"/></svg>12% reduction in average service turnaround time</li>
      <li><svg><use href="#tick-dot"/></svg>Customer satisfaction up from 89% to 94%</li>
      <li><svg><use href="#tick-dot"/></svg>Fleet utilization efficiency improved by 15%</li>
    </ul>
  </div>
  <div class="page-no">05</div>
</section>

<!-- 06 Operations table -->
<section class="slide col-r row3">
  <svg class="corner"><use href="#corner-sweep"/></svg>
  <h2 class="slide-title">Operational Metrics Summary – <em>Q3 2025</em></h2>
  <div class="brand-tag">Keystone Lane<br>Gauging</div>
  <table class="ops-table">
    <colgroup><col style="width:104px"><col style="width:122px"><col style="width:68px"><col style="width:65px"><col></colgroup>
    <thead><tr><th>CATEGORY</th><th>METRIC</th><th>Q2 2025</th><th>Q3 2025</th><th>CHANGE <small>(%)</small></th></tr></thead>
    <tbody>
      <tr><td>Service Appointments</td><td>Completed Jobs</td><td>248</td><td>296</td><td>+19.4%</td></tr>
      <tr><td>Calibration Turnaround Time</td><td>Avg. Days to Complete</td><td>4.3</td><td>3.1</td><td>-27.9%</td></tr>
      <tr><td>Equipment Sales</td><td>Units Sold</td><td>85</td><td>102</td><td>+20.0%</td></tr>
      <tr><td>Maintenance Contracts</td><td>Active Contracts</td><td>121</td><td>138</td><td>+14.0%</td></tr>
      <tr><td>Customer Satisfaction</td><td>Average Rating (1–5)</td><td>4.4</td><td>4.6</td><td>+4.5%</td></tr>
    </tbody>
  </table>
  <div class="page-no">06</div>
</section>

<!-- 07 Affiliates -->
<section class="slide col-l row4">
  <svg class="corner"><use href="#corner-sweep"/></svg>
  <h2 class="slide-title">Our Three <em>Affiliates</em></h2>
  <div class="brand-tag">Keystone Lane<br>Gauging</div>
  <div class="affiliate" style="left:20px">
    <div class="affiliate-name"><i></i>Fernway Balance</div>
    <p style="margin-top:10px">Fernway Balance was established in 2004 and proudly serves the midwest and west regions including colorado, wyoming, and iowa, offering the highest quality products</p>
  </div>
  <div class="affiliate" style="left:166px">
    <div class="affiliate-name" style="height:48px"><i></i>Meadowlark Handling<br>&amp; Massing</div>
    <p style="margin-top:4px">At Meadowlark Handling &amp; Massing, we hold ourselves to the highest standards of honesty and integrity. Our commitment to providing exceptional products and services goes above and beyond what our customers expect.</p>
  </div>
  <div class="affiliate" style="left:313px">
    <div class="affiliate-name"><i></i>TV Balance</div>
    <p style="margin-top:10px">TV Balance also develops custom weighing solutions for a wide variety of customer needs. We can design specifically for your needs, and our projects can include high-speed check weighing</p>
  </div>
  <div class="page-no">07</div>
</section>

<!-- 08 Closing -->
<section class="slide col-r row4">
  <div class="closing-bg" role="img" aria-label="Dimmed photo of a scale workshop interior with shelving and a service truck"></div>
  <div class="closing-brand">Keystone Lane<br>Gauging</div>
  <div class="closing-thanks">THANK YOU</div>
</section>

</body>
</html>
```